A4 Single Sided Brochure Folder Design Technical Company

We are a technical company based in the UK, working worldwide for Power Distribution companies.

We have technical literature and need a folder to present these in. The design should be very simple and clean using our logo and "Innovative Utility Solutions"

Our website kestrome.com gives and idea of the business but don't follow the look of the website as we will be redoing shortly.

• Logo and Strap Line
• Clean, easy to print and timeless
• Shouldn't be fashionable, we certainly aren't

```html
<!DOCTYPE html>
<html lang="en">
<head>
<meta charset="utf-8">
<title>Kestrome – A4 Presentation Folder</title>
<link rel="stylesheet" href="https://fonts.googleapis.com/css2?family=Lato:wght@300;400&family=Quicksand:wght@500&display=swap">
<style>
  :root {
    --backdrop: #e6e2dd;
    --paper: #ffffff;
    --fold-line: #cfc8c0;
    --brand-magenta: #b5338c;
    --tagline-grey: #9a9a9a;
    --url-grey: #555555;
  }
  html, body {
    margin: 0;
    padding: 0;
    width: 1200px;
    height: 1200px;
    overflow: hidden;
    background: var(--backdrop);
  }
  .folder {
    position: relative;
    width: 1200px;
    height: 1200px;
  }
  .folder-dieline {
    position: absolute;
    left: 0;
    top: 0;
  }
  .brand-name {
    position: absolute;
    left: 716px;
    top: 552px;
    margin: 0;
    font-family: "Quicksand", sans-serif;
    font-weight: 500;
    font-size: 60px;
    line-height: 1;
    color: var(--brand-magenta);
    white-space: nowrap;
  }
  .brand-tagline {
    position: absolute;
    left: 762px;
    top: 616px;
    margin: 0;
    font-family: "Lato", sans-serif;
    font-weight: 300;
    font-size: 25px;
    line-height: 1.2;
    color: var(--tagline-grey);
    white-space: nowrap;
  }
  .web-address {
    position: absolute;
    left: 134px;
    top: 778px;
    margin: 0;
    font-family: "Lato", sans-serif;
    font-weight: 400;
    font-size: 12px;
    color: var(--url-grey);
  }
</style>
</head>
<body>
  <main class="folder">
    <svg class="folder-dieline" width="1200" height="1200" viewBox="0 0 1200 1200" aria-hidden="true">
      <rect class="cover-panel" x="95" y="150" width="994" height="694" fill="var(--paper)"/>
      <rect class="cover-stripe" x="95" y="830" width="994" height="6" fill="var(--brand-magenta)"/>
      <polygon class="pocket-flap" points="60,854 95,844 592,844 522,1050 95,1050 60,1044" fill="var(--paper)"/>
      <line class="pocket-fold" x1="95" y1="844" x2="95" y2="1050" stroke="var(--fold-line)" stroke-width="1"/>
      <line class="pocket-fold" x1="95" y1="844" x2="592" y2="844" stroke="var(--fold-line)" stroke-width="1"/>
    </svg>

    <h1 class="brand-name">Kestrome</h1>
    <p class="brand-tagline">Innovative Utility Solutions</p>

    <p class="web-address">www.kestrome.com</p>
  </main>
</body>
</html>
```